Merrowin Vodka logo and label design

We would like a logo and bottle label design for a new line of Ultra-Premium Vodka. The Company is called Merrowin Spirits and is based in Brisbane, Australia. We would like a 'Gatsby/Prohibition era vibe to the design. We want to keep it minimalistic and sleek. We strongly prefer a minimalist design and colour palette. Black,Gold,Grey,White,Silver,Red and Blue

The bottle will be similar in shape to Castellane/Blue Heron. There will also need to be space on the label for required information, as well as short bio of the company, which will be provided to the winning design.
Updates

We would like to add the polish code of arms for Opoczno. Have attached link for reference. https://www.crestarchive-demo.net/crestwiki/index.php?title=Opoczno

Target Market(s)

Luxury brand customers

Logo Text

Merrowin Ultra-Premium Vodka

Logo styles of interest
Wordmark Logo
Lettermark Logo
Requirements
Must have
• This is the first release from our new Vodka label. We want a logo and bottle label that reflects a premium product. We very much like Prohibition/Gatsby era themed bottles and labels. The label and bottle should be elegant and clean.
Should not have
• Anything too busy or confusing.

```html
<!DOCTYPE html>
<html lang="en">
<head>
<meta charset="utf-8">
<title>Merrowin Ultra-Premium Vodka – Label</title>
<link rel="stylesheet" href="https://fonts.googleapis.com/css2?family=Cormorant+Garamond:wght@500&family=Montserrat:wght@600&display=swap">
<style>
  :root {
    --page-bg: #ffffff;
    --gold-light: #f3d77e;
    --gold-mid: #d4a73c;
    --gold-deep: #a8761f;
    --gold-text: #e9c563;
    --black-edge: #0b0b0b;
    --black-mid: #1f1f1f;
    --black-sheen: #333333;
  }
  html, body {
    margin: 0;
    padding: 0;
    width: 689px;
    height: 1200px;
    overflow: hidden;
    background: var(--page-bg);
  }
  .canvas {
    position: relative;
    width: 689px;
    height: 1200px;
  }
  .label {
    position: absolute;
    left: 64px;
    top: 268px;
    width: 560px;
    height: 663px;
  }
  .label-shield {
    position: absolute;
    inset: 0;
    width: 100%;
    height: 100%;
  }
  .brand-mark {
    position: absolute;
    left: 50%;
    top: 140px;
    width: 100px;
    height: 100px;
    margin-left: -50px;
    border-radius: 50%;
    background: var(--gold-mid);
  }
  .brand-name {
    position: absolute;
    left: 0;
    right: 0;
    top: 312px;
    margin: 0;
    text-align: center;
    font-family: "Cormorant Garamond", Georgia, serif;
    font-weight: 500;
    font-size: 92px;
    line-height: 1;
    letter-spacing: 0.01em;
    color: var(--gold-text);
  }
  .brand-tagline {
    position: absolute;
    left: 0;
    right: 0;
    top: 404px;
    margin: 0;
    text-align: center;
    font-family: "Montserrat", Arial, sans-serif;
    font-weight: 600;
    font-size: 17px;
    line-height: 1;
    letter-spacing: 0.42em;
    padding-left: 0.42em;
    color: var(--gold-text);
  }
</style>
</head>
<body>
<main class="canvas">
  <section class="label" aria-label="Merrowin Ultra-Premium Vodka bottle label">
    <svg class="label-shield" viewBox="0 0 490 580" aria-hidden="true">
      <defs>
        <linearGradient id="goldFrame" x1="0" y1="0" x2="1" y2="1">
          <stop offset="0" stop-color="var(--gold-light)"/>
          <stop offset="0.5" stop-color="var(--gold-mid)"/>
          <stop offset="1" stop-color="var(--gold-deep)"/>
        </linearGradient>
        <linearGradient id="blackField" x1="0" y1="0" x2="1" y2="0">
          <stop offset="0" stop-color="var(--black-edge)"/>
          <stop offset="0.3" stop-color="var(--black-mid)"/>
          <stop offset="0.58" stop-color="var(--black-sheen)"/>
          <stop offset="0.8" stop-color="var(--black-mid)"/>
          <stop offset="1" stop-color="var(--black-edge)"/>
        </linearGradient>
      </defs>
      <path class="shield-frame" d="M0,0 H490 V330 A245,250 0 0 1 0,330 Z" fill="url(#goldFrame)"/>
      <path class="shield-field" d="M12,12 H478 V330 A233,238 0 0 1 12,330 Z" fill="url(#blackField)"/>
    </svg>
    <span class="brand-mark" aria-hidden="true"></span>
    <h1 class="brand-name">MERROWIN</h1>
    <p class="brand-tagline">ULTRA-PREMIUM VODKA</p>
  </section>
</main>
</body>
</html>
```